Property Finance Company - Orbin Funding Limited

Background: Orbin Funding Group Limited is a private property finance company. Orbin Funding Group has capital to directly fund first mortgage, mezzanine and preferred equity financing. We also acquire performing, sub-performing and distressed debt.

Orbin Fundings management philosophy emphasises expertise, innovation, wisdom, honesty and competitiveness. Orbin Funding are not finance brokers - we provide debt funding to the commercial property and residential development sectors. Our process is built from experience and cumutavely Orbin Fundings Directors have in excess of 60 years wisdom.

The aim of the website will be to increase brand awareness, provide clients with comfort around our level of skill and background on who we are, generate more sales, and provide examples of projects that we have funded.

The website is a new product launch, and we need to use our Orbin Funding logo that has just been designed. We like a dark background, and either black/silver/grey/ jade green, or black/gold/jade green colours.

Our unique advantages are that we have fast turnaround times, we can solve clients funding problems and we know what we are doing. Our target audience will be viewing the website on both desktop and mobile devices.

We would like to have the following pages:

Home
About
Team
Services
Project Experience
Contact

Competitors Website: http://www.tarvolo.example/

We would also like to have the option of video footage in our website, as you can see in our competitors website.

Overall we want a really slick, elegant but modern website that is better than www.tarvolo.example

Target Market(s)

Finance borrowers, property developers, accountants, lawyers, businesspeople, high net worth people

Industry/Entity Type

Finance

Requirements
Must have
• Please see project description
Nice to have
Should not have

```html
<!DOCTYPE html>
<html lang="en">
<head>
<meta charset="utf-8">
<title>Orbin Funding Group</title>
<link rel="stylesheet" href="https://fonts.googleapis.com/css2?family=Gelasio:wght@400&family=Lato:wght@400;700&family=Montserrat:wght@600;700&display=swap">
<style>
:root{
  --ink:#1f1f1f;
  --white:#ffffff;
  --muted:#c9c9c9;
  --soft:#9a9a9a;
  --band:#f4f4f4;
  --line:#ececec;
  --icon:#c4c4c4;
  --icon-dark:#2e2e2e;
  --footer:#151515;
  --serif:"Gelasio", Georgia, serif;
  --sans:"Lato", Arial, sans-serif;
  --display:"Montserrat", Arial, sans-serif;
}
*{box-sizing:border-box;margin:0;padding:0}
html,body{width:1200px;height:2568px;overflow:hidden}
body{position:relative;background:var(--white);font-family:var(--sans);color:var(--ink)}
h1,h2{font-weight:400}
.abs{position:absolute}

/* hero */
.hero{left:0;top:0;width:1200px;height:676px;background:linear-gradient(160deg,#3a3a3a 0%,#1b1b1b 35%,#4a4a4a 60%,#2a2a2a 100%)}
.brand{left:70px;top:22px;width:190px;display:flex;flex-direction:column;align-items:center;color:var(--white)}
.brand-mark{display:block;flex-shrink:0;width:56px;height:56px;border-radius:50%;background:var(--white);margin-bottom:10px}
.brand-name{font-family:var(--serif);font-size:22px;line-height:1.2;text-align:center;letter-spacing:1px}
.nav{left:411px;top:84px;width:714px;display:flex;justify-content:space-between;font-family:var(--serif);font-size:13px;letter-spacing:.5px;color:#cfcfcf}
.nav .active{color:var(--white)}
.hero-title{left:79px;top:290px;font-family:var(--display);font-weight:700;font-size:76px;color:var(--white);letter-spacing:1px;line-height:1}
.hero-lead{left:79px;top:386px;width:660px;font-weight:700;font-size:21px;line-height:28px;color:var(--white)}
.btn{top:463px;height:51px;border-radius:26px;font-family:var(--display);font-weight:600;font-size:18px;display:flex;align-items:center;justify-content:center;letter-spacing:.5px}
.btn-solid{left:77px;width:188px;background:var(--white);color:var(--ink)}
.btn-ghost{left:276px;width:186px;border:2px solid var(--white);color:var(--white)}

/* about */
.section-title{font-family:var(--serif);font-size:40px;color:var(--ink);text-align:center;width:1200px;left:0;letter-spacing:.5px;line-height:1.2}
.about-title{top:724px}
.about-text{left:103px;top:790px;width:994px;font-size:13px;line-height:19px;text-align:center;color:var(--muted)}
.values{left:183px;top:885px;width:834px;height:240px;border:1px solid var(--line)}
.value{position:absolute;top:0;width:209px;height:238px;text-align:center;border-right:1px solid var(--line)}
.value.raised{top:-2px;height:230px;background:var(--white);box-shadow:0 8px 22px rgba(0,0,0,.18);z-index:2;border:none}
.value-icon{width:103px;height:103px;border-radius:50%;background:var(--icon);margin:22px auto 0;display:flex;align-items:center;justify-content:center}
.raised .value-icon{background:var(--icon-dark)}
.value-name{font-family:var(--serif);font-size:20px;color:#6a6a6a;margin-top:16px}
.raised .value-name{color:var(--ink)}
.value-desc{font-size:13px;line-height:19px;color:var(--muted);margin:8px 16px 0}

/* services */
.services{left:0;top:1186px;width:1200px;height:471px;background:var(--band)}
.services-title{top:1236px}
.service{top:1313px;width:248px;height:291px;background:var(--white)}
.service-img{width:248px;height:166px}
.service-name{font-family:var(--serif);font-size:18px;line-height:22px;margin:16px 12px 0;color:var(--ink)}
.service-name.long{font-size:17px;letter-spacing:-.3px;margin-top:12px}
.service-desc{font-size:13px;line-height:19px;color:var(--muted);margin:10px 12px 0}
.service-btn{left:51px;top:54px;width:146px;height:52px;border-radius:26px;background:var(--white);font-family:var(--display);font-weight:600;font-size:14px;display:flex;align-items:center;justify-content:center}

/* testimonial / work */
.col-title{font-family:var(--serif);font-size:40px;color:var(--ink);letter-spacing:.5px;line-height:1.2}
.quote{left:79px;top:1774px;width:560px;font-size:13px;line-height:26px;color:var(--muted)}
.quote-mark{display:inline-block;height:14px;font-family:var(--serif);font-size:40px;color:#d8d8d8;line-height:1;vertical-align:-8px;overflow:visible}
.quote-mark.close{vertical-align:-22px;margin-left:6px}
.avatar{left:92px;top:1890px;width:118px;height:118px;border-radius:50%;border:4px solid var(--white);box-shadow:0 0 0 2px #dcdcdc,0 10px 14px -8px rgba(0,0,0,.35);background:linear-gradient(160deg,#8fb7d9,#e9d6b8 60%,#3a3a3a)}
.client{left:252px;top:1926px}
.client-name{font-family:var(--serif);font-size:20px;color:var(--ink)}
.client-place{font-size:13px;letter-spacing:1px;color:var(--soft);font-style:italic}
.work-thumb{width:113px;height:113px;border:4px solid var(--white);box-shadow:0 0 0 1px #e3e3e3}
.work-title{font-family:var(--serif);font-size:16px;color:var(--ink)}
.work-text{font-size:13px;line-height:20px;color:var(--muted);width:280px;margin-top:8px}

/* contact */
.contact{left:0;top:2072px;width:1200px;height:436px;background:linear-gradient(180deg,#2b3442 0%,#1c2430 55%,#2f3a3f 100%)}
.contact-panel{left:339px;top:2136px;width:521px;height:372px;background:rgba(255,255,255,.14)}
.contact-title{left:339px;top:2182px;width:521px;text-align:center;font-family:var(--serif);font-size:40px;color:var(--white);line-height:1.2}
.c-icon{width:54px;height:54px;border-radius:50%;background:var(--white);display:flex;align-items:center;justify-content:center}
.c-text{color:var(--white);font-size:16px;white-space:nowrap}
.c-text.bold{font-weight:700}
.social{width:40px;height:40px;border-radius:50%;background:var(--white);top:2375px}
.social.outline{background:transparent;border:2px solid var(--white)}
.footer{left:0;top:2508px;width:1200px;height:60px;background:var(--footer);color:#8a8a8a;font-size:13px;display:flex;align-items:center;justify-content:center}
.footer b{color:#cfcfcf;font-weight:400}
</style>
</head>
<body>

<!-- Hero -->
<div class="abs hero" role="img" aria-label="Black and white view looking up at city skyscrapers"></div>
<div class="abs brand">
  <span class="brand-mark"></span>
  <span class="brand-name">ORBIN FUNDING<br>GROUP</span>
</div>
<nav class="abs nav">
  <span class="active">HOME</span><span>ABOUT US</span><span>SERVICES</span><span>TEAM</span><span>PROJECTS</span><span>CONTACT US</span>
</nav>
<h1 class="abs hero-title">FUNDARO</h1>
<p class="abs hero-lead">We help you managing asset, provide financial advice.Leave money issue with us and focus on your core business.</p>
<a class="abs btn btn-solid">GET STARTED</a>
<a class="abs btn btn-ghost">LEARN MORE</a>

<!-- About -->
<h2 class="abs section-title about-title">ABOUT ORBIN FUNDING GROUP</h2>
<p class="abs about-text">Lorem Ipsum is simply dummy text of the printing and typesetting industry. Lorem Ipsum has been the.Lorem Ipsum is simply dummy text of the printing and typesetting industry. Lorem Ipsum has been the.Lorem Ipsum is simply dummy text of the printing and typesetting industry.Lorem Ipsum is simply dummy text of the printing and typesetting industry. Lorem Ipsum has been the.</p>
<div class="abs values">
  <div class="value" style="left:0">
    <div class="value-icon"><svg width="44" height="50" viewBox="0 0 44 50"><circle cx="22" cy="18" r="14" fill="none" stroke="#444" stroke-width="3"/><rect x="15" y="34" width="14" height="9" fill="#444"/><rect x="17" y="45" width="10" height="3" fill="#444"/></svg></div>
    <div class="value-name">Innovation</div>
    <div class="value-desc">Lorem Ipsum is simply dummy text of the printin.</div>
  </div>
  <div class="value raised" style="left:209px">
    <div class="value-icon"></div>
    <div class="value-name">Wisdome</div>
    <div class="value-desc">Lorem Ipsum is simply dummy text of the printin.</div>
  </div>
  <div class="value" style="left:418px">
    <div class="value-icon"><svg width="56" height="36" viewBox="0 0 56 36"><path d="M2 10 L16 4 L28 10 L40 4 L54 10 L48 24 L34 32 L22 32 L8 24 Z" fill="#555"/></svg></div>
    <div class="value-name">Honesty</div>
    <div class="value-desc">Lorem Ipsum is simply dummy text of the printin.</div>
  </div>
  <div class="value" style="left:627px;border-right:none">
    <div class="value-icon"><svg width="52" height="52" viewBox="0 0 52 52"><circle cx="26" cy="22" r="16" fill="none" stroke="#444" stroke-width="3"/><path d="M10 22h32M26 6v32" stroke="#444" stroke-width="2"/><circle cx="12" cy="44" r="4" fill="#444"/><circle cx="26" cy="46" r="4" fill="#444"/><circle cx="40" cy="44" r="4" fill="#444"/></svg></div>
    <div class="value-name">Competitiveness</div>
    <div class="value-desc">Lorem Ipsum is simply dummy text of the printin.</div>
  </div>
</div>

<!-- Services -->
<div class="abs services"></div>
<h2 class="abs section-title services-title">OUR SERVICES</h2>
<div class="abs service" style="left:79px">
  <div class="service-img" role="img" aria-label="Dim photo of stacked coins" style="background:linear-gradient(135deg,#3b342c,#6f6252)"></div>
  <a class="abs service-btn">LEARN MORE</a>
  <div class="service-name">Debt funding</div>
  <div class="service-desc">Lorem Ipsum is simply dummy text of the printing and typesetting industry.</div>
</div>
<div class="abs service" style="left:343px">
  <div class="service-img" role="img" aria-label="City street with old buildings and a red phone box" style="background:linear-gradient(180deg,#b7bcc2,#6d6a66 60%,#3c3a38)"></div>
  <div class="service-name">Mezzanine</div>
  <div class="service-desc">Lorem Ipsum is simply dummy text of the printing and typesetting industry.</div>
</div>
<div class="abs service" style="left:608px">
  <div class="service-img" role="img" aria-label="Calculator, glasses and coins beside an equity sign" style="background:linear-gradient(135deg,#c98f6a,#7a5a45 55%,#2e3b4a)"></div>
  <div class="service-name">Equity financing</div>
  <div class="service-desc">Lorem Ipsum is simply dummy text of the printing and typesetting industry.</div>
</div>
<div class="abs service" style="left:872px">
  <div class="service-img" role="img" aria-label="Person reviewing papers in a bright living room" style="background:linear-gradient(135deg,#f1efec,#d9d4ce 60%,#8fa3b8)"></div>
  <div class="service-name long">Perdorming,sub-performing<br>and distressed debt</div>
  <div class="service-desc">Lorem Ipsum is simply dummy text of the printing.</div>
</div>

<!-- Testimonial -->
<h2 class="abs col-title" style="left:79px;top:1702px">TESTIMONIAL</h2>
<p class="abs quote"><span class="quote-mark">&ldquo;</span>Lorem Ipsum is simply dummy text of the printing and typesetting industry. Lorem Ipsum has been the industry's standard dummy text ever since the 1500s, when an unknown printer took a galley of type and scrambled it to make a type specimen book. It has survived not only five centuries.<span class="quote-mark close">&rdquo;</span></p>
<div class="abs avatar" role="img" aria-label="Client portrait"></div>
<div class="abs client">
  <div class="client-name">- Client Name</div>
  <div class="client-place">LONDON</div>
</div>

<!-- Our work -->
<h2 class="abs col-title" style="left:697px;top:1702px">OUR WORK</h2>
<div class="abs work-thumb" style="left:697px;top:1770px;background:linear-gradient(135deg,#6f8f4a,#b58a5a 60%,#5a4a3a)" role="img" aria-label="Village houses on a green hillside"></div>
<div class="abs" style="left:823px;top:1770px">
  <div class="work-title">Lorem Ipsum is simply dummy</div>
  <div class="work-text">Lorem Ipsum is simply dummy text of the printing and typesetting industry. Lorem Ipsum has been the industry's standard dummy text ever since the 1500s.</div>
</div>
<div class="abs work-thumb" style="left:697px;top:1905px;background:linear-gradient(135deg,#9fb4c8,#3d4f63 60%,#cfd6dc)" role="img" aria-label="Business handshake"></div>
<div class="abs" style="left:823px;top:1905px">
  <div class="work-title">Lorem Ipsum is simply dummy</div>
  <div class="work-text">Lorem Ipsum is simply dummy text of the printing and typesetting industry. Lorem Ipsum has been the industry's standard dummy text ever since the 1500s.</div>
</div>

<!-- Contact -->
<div class="abs contact" role="img" aria-label="Dusk aerial view of a city skyline by the water"></div>
<div class="abs contact-panel"></div>
<h2 class="abs contact-title">CONTACT US</h2>
<div class="abs c-icon" style="left:380px;top:2253px"><svg width="24" height="24" viewBox="0 0 24 24"><path d="M6 3l4 4-2 3c1 2 4 5 6 6l3-2 4 4-3 3C10 21 3 14 3 6z" fill="none" stroke="#333" stroke-width="1.6"/></svg></div>
<div class="abs c-text bold" style="left:447px;top:2270px">123 456 7878</div>
<div class="abs c-icon" style="left:579px;top:2253px"><svg width="24" height="24" viewBox="0 0 24 24"><rect x="3" y="6" width="18" height="13" rx="1" fill="none" stroke="#333" stroke-width="1.6"/><path d="M3 7l9 7 9-7" fill="none" stroke="#333" stroke-width="1.6"/></svg></div>
<div class="abs c-text" style="left:645px;top:2270px;font-size:15px">info@orbinfundinggroup.example</div>
<div class="abs c-icon" style="left:380px;top:2317px"><svg width="24" height="24" viewBox="0 0 24 24"><path d="M12 22s7-7 7-12a7 7 0 0 0-14 0c0 5 7 12 7 12z" fill="none" stroke="#333" stroke-width="1.6"/><circle cx="12" cy="10" r="2.5" fill="none" stroke="#333" stroke-width="1.6"/></svg></div>
<div class="abs c-text" style="left:447px;top:2335px;font-size:14px">123 Lorem ipsum dummy text,Country - 123 456..</div>
<span class="abs social" style="left:502px"></span>
<span class="abs social outline" style="left:554px"></span>
<span class="abs social outline" style="left:607px"></span>
<span class="abs social outline" style="left:658px"></span>

<footer class="abs footer">©&nbsp;<b>ORBIN FUNDING GROUP</b>&nbsp;- 2017. All Rights Reserved</footer>

</body>
</html>
```